RESIDENTIAL CONSTRUCTION

We are a company that specializes in building custom residential homes, the design should also emphasize that quality and service is our priority.

Industry/Entity Type

Construction Company

Contact Information for Business Card

Contact Person: Marcus Lindqvist
Company Address: 273 West Alder Ave San Jose , Ca 95380
Phone Number : 408-731-2946
Email Address: Stoneridgehomes517@mailvista.net

Font styles to use
Sans Serif

Colors
ec1f27

Requirements
Must have
• CSLB # 7362015
Nice to have
• needs to have same color as logo i uploaded, we will be printing these on a clear plastic card.

```html
<!DOCTYPE html>
<html lang="en">
<head>
<meta charset="utf-8">
<title>Stoneridge General Builders – Business Card</title>
<link href="https://fonts.googleapis.com/css2?family=Roboto:wght@400;700&display=swap" rel="stylesheet">
<style>
  :root {
    --brand-red: #ec1f27;
    --deep-red: #b0232b;
    --ink: #4a4a4a;
    --card: #ffffff;
    --backdrop: #e9e9eb;
  }
  html, body {
    margin: 0;
    padding: 0;
    width: 1200px;
    height: 802px;
    overflow: hidden;
    background: var(--backdrop);
  }
  .canvas {
    position: relative;
    width: 1200px;
    height: 802px;
  }
  .business-card {
    position: absolute;
    left: 75px;
    top: 101px;
    width: 1050px;
    height: 600px;
    background: var(--card);
    box-shadow: 0 6px 24px rgba(0, 0, 0, 0.12);
    font-family: "Roboto", Arial, sans-serif;
    color: var(--ink);
  }
  .brand-name {
    position: absolute;
    left: 72px;
    top: 62px;
    margin: 0;
    font-size: 44px;
    font-weight: 700;
    line-height: 1.05;
    color: var(--deep-red);
    text-transform: uppercase;
    letter-spacing: 1px;
  }
  .brand-name .brand-line {
    display: block;
  }
  .contact-block {
    position: absolute;
    left: 72px;
    top: 200px;
  }
  .contact-name {
    margin: 0 0 14px;
    font-size: 30px;
    font-weight: 700;
    color: var(--deep-red);
    text-transform: uppercase;
    letter-spacing: 0.5px;
  }
  .address {
    margin: 0;
    font-style: normal;
    font-size: 22px;
    line-height: 30px;
  }
  .license {
    margin: 0 0 10px;
    font-size: 22px;
    line-height: 30px;
  }
  .contact-list {
    list-style: none;
    margin: 0;
    padding: 0;
    font-size: 22px;
    line-height: 32px;
  }
  .contact-list li {
    display: flex;
    align-items: center;
    gap: 12px;
  }
  .contact-icon {
    width: 18px;
    height: 18px;
    flex: none;
  }
  .corner-mark {
    position: absolute;
    right: 70px;
    bottom: 70px;
    display: flex;
    align-items: center;
    gap: 10px;
    font-size: 22px;
    font-weight: 700;
    color: var(--deep-red);
    text-transform: uppercase;
    letter-spacing: 1px;
  }
  .corner-mark .mark-square {
    width: 16px;
    height: 16px;
    background: var(--deep-red);
  }
</style>
</head>
<body>
<div class="canvas">
  <section class="business-card">
    <h1 class="brand-name">
      <span class="brand-line">Stoneridge</span>
      <span class="brand-line">General Builders</span>
    </h1>

    <div class="contact-block">
      <h2 class="contact-name">Marcus Lindqvist</h2>
      <address class="address">
        273 West Alder Ave San Jose<br>
        Ca 95380
      </address>
      <p class="license">CSLB # 7362015</p>
      <ul class="contact-list">
        <li>
          <svg class="contact-icon" viewBox="0 0 24 24" aria-hidden="true">
            <path fill="var(--deep-red)" d="M6.6 10.8a15.1 15.1 0 0 0 6.6 6.6l2.2-2.2a1 1 0 0 1 1-.25 11.4 11.4 0 0 0 3.6.57 1 1 0 0 1 1 1V20a1 1 0 0 1-1 1A17 17 0 0 1 3 4a1 1 0 0 1 1-1h3.5a1 1 0 0 1 1 1c0 1.25.2 2.45.57 3.57a1 1 0 0 1-.25 1z"/>
          </svg>
          <span>408-731-2946</span>
        </li>
        <li>
          <svg class="contact-icon" viewBox="0 0 24 24" aria-hidden="true">
            <rect x="2" y="5" width="20" height="14" rx="1.5" fill="var(--deep-red)"/>
            <path d="M3 6.5l9 6.5 9-6.5" fill="none" stroke="#fff" stroke-width="1.6"/>
          </svg>
          <span>Stoneridgehomes517@mailvista.net</span>
        </li>
        <li>
          <svg class="contact-icon" viewBox="0 0 24 24" aria-hidden="true">
            <circle cx="12" cy="12" r="10" fill="var(--deep-red)"/>
            <ellipse cx="12" cy="12" rx="4" ry="10" fill="none" stroke="#fff" stroke-width="1.4"/>
            <path d="M2 12h20" stroke="#fff" stroke-width="1.4"/>
          </svg>
          <span>www.stoneridgebuilders.net</span>
        </li>
      </ul>
    </div>

    <div class="corner-mark">
      <span class="mark-square"></span>
      <span>Stoneridge</span>
    </div>
  </section>
</div>
</body>
</html>
```